Vantiqo custom business card design

Need a authentic, innovative business card design for a new mobile app business. I am uploading a few screen images from our app for you to view. I would like app design theme to match business card design. I can also send logo images.

```html
<!DOCTYPE html>
<html lang="en">
<head>
<meta charset="utf-8">
<title>Vantiqo Business Card</title>
<link rel="stylesheet" href="https://fonts.googleapis.com/css2?family=Lato:wght@400;700;900&display=swap">
<style>
  :root {
    --stage: #d9d9db;
    --card-white: #ffffff;
    --card-dark: #1d1d1d;
    --pattern-tone: #2c2c2c;
    --brand-purple: #6a0b9c;
    --ink: #161616;
    --divider: #e2e2e2;
  }
  * { box-sizing: border-box; margin: 0; padding: 0; }
  html, body { width: 1200px; height: 782px; overflow: hidden; }
  body {
    background: var(--stage);
    font-family: "Lato", sans-serif;
    display: flex;
    align-items: center;
    justify-content: center;
    gap: 40px;
  }
  .card {
    width: 540px;
    height: 309px;
    position: relative;
    box-shadow: 0 6px 18px rgba(0,0,0,0.18);
  }
  .card-front {
    background: var(--card-white);
    display: flex;
    align-items: center;
    padding: 0 34px 0 40px;
  }
  .brand-block {
    width: 200px;
    display: flex;
    flex-direction: column;
    align-items: center;
    gap: 14px;
  }
  .brand-dot {
    width: 92px;
    height: 92px;
    border-radius: 50%;
    background: var(--brand-purple);
  }
  .brand-name {
    font-weight: 900;
    font-size: 38px;
    color: var(--ink);
    letter-spacing: 0.5px;
  }
  .divider {
    width: 1px;
    height: 170px;
    background: var(--divider);
    margin: 0 26px 0 22px;
  }
  .contact-block { color: var(--ink); }
  .person-name {
    font-weight: 900;
    font-size: 20px;
    color: var(--brand-purple);
    letter-spacing: 0.6px;
    text-transform: uppercase;
    line-height: 1;
  }
  .person-role {
    font-size: 15px;
    margin: 3px 0 6px;
  }
  .contact-list { list-style: none; }
  .contact-item {
    display: flex;
    align-items: center;
    gap: 6px;
    font-size: 15px;
    line-height: 1.3;
  }
  .contact-icon { width: 12px; height: 12px; flex: none; fill: var(--brand-purple); }
  .address { font-size: 15px; line-height: 1.3; margin-top: 2px; }
  .card-back {
    background: var(--card-dark);
    overflow: hidden;
  }
  .back-pattern {
    position: absolute;
    inset: 0;
    background: radial-gradient(circle at 50% 50%, var(--pattern-tone), var(--card-dark));
  }
  .back-mark {
    position: absolute;
    right: 60px;
    bottom: 60px;
    display: flex;
    align-items: center;
    gap: 10px;
  }
  .back-dot { width: 28px; height: 28px; border-radius: 50%; background: var(--card-white); }
  .back-name { font-weight: 900; font-size: 20px; color: var(--card-white); }
</style>
</head>
<body>
  <section class="card card-front">
    <div class="brand-block">
      <div class="brand-dot"></div>
      <div class="brand-name">Vantiqo</div>
    </div>
    <div class="divider"></div>
    <div class="contact-block">
      <p class="person-name">Marcus Hale</p>
      <p class="person-role">Managing Director</p>
      <ul class="contact-list">
        <li class="contact-item">
          <svg class="contact-icon" viewBox="0 0 12 12"><path d="M1 4c0-2 2-3 5-3s5 1 5 3v1H8V4H4v1H1zM2 6h8l1 5H1z"/></svg>
          061-870 245 316
        </li>
        <li class="contact-item">
          <svg class="contact-icon" viewBox="0 0 12 12"><path d="M3 0h6v12H3zM4 1.5v8h4v-8z"/></svg>
          061-870 245 317
        </li>
        <li class="contact-item">
          <svg class="contact-icon" viewBox="0 0 12 12"><path d="M0 2h12v8H0zM1 3l5 4 5-4z" fill-rule="evenodd"/></svg>
          hello@vantiqo.app
        </li>
        <li class="contact-item">
          <svg class="contact-icon" viewBox="0 0 12 12"><circle cx="6" cy="6" r="6"/></svg>
          www.vantiqo.app
        </li>
      </ul>
      <p class="address">48 Linden Quay, Suite 7<br>Harbour City, 204815.</p>
    </div>
  </section>

  <section class="card card-back">
    <div class="back-pattern" role="img" aria-label="Repeating tonal pattern of the brand symbol on dark charcoal"></div>
    <div class="back-mark">
      <div class="back-dot"></div>
      <span class="back-name">Vantiqo</span>
    </div>
  </section>
</body>
</html>
```